Allied Health team of Physiotherapists & Occupational Therapists seek a business card design

We have our new logo, we now need our new business cards and stationary. Tidewell: Oedema & Family Clinic is seeking a generic card design to represent our whole team and individual cards for each therapist that incorporates our new logo to communicate our holistic approach that is calming, nuturing, supportive and welcoming.
Our Physiotherapists and Occupational Therapists assess, treat and provide education for people who are at risk of or who have lymphoedema. This is often as a result of treatment for cancer. We provide pre-operative and post-operative management and cancer rehabilitation in our Pilates studio. Our team also consists of Physiotherapists who have a strong interest in pelvic floor and continence management for both men and women.

Target Market(s)

Mainly women health conscious

Industry/Entity Type

Allied Health: Physiotherapy / Occupational Therapy

Contact Information for Business Card

Address: 14 Gallivant Ave Marlowe Bay 3942 Phone: 84316570 fax: 8431 6578 Email: info@tidewellcareservices.com.au Website: tidewellcareservices.com.au Facebook address: facebook.com/TidewellOedemaAndFamilyCareClinic. Room to write appointments. Individual cards need to have name, office email and individual email and professional details

Requirements
Must have
• Logo as per uploaded documents

```html
<!DOCTYPE html>
<html lang="en">
<head>
<meta charset="utf-8">
<title>Tidewell Business Card</title>
<link rel="stylesheet" href="https://fonts.googleapis.com/css2?family=Philosopher:wght@700&family=Nunito+Sans:wght@400;600&family=Montserrat:ital,wght@0,500;1,700;1,800&display=swap">
<style>
  :root {
    --backdrop: #2b2b2b;
    --card: #ffffff;
    --peach: #f8b07f;
    --peach-text: #f5a878;
    --sage: #c3cdbf;
    --ink-white: #ffffff;
    --dots: #8a8a8a;
  }
  * { margin: 0; padding: 0; box-sizing: border-box; }
  html, body {
    width: 1200px; height: 1200px; overflow: hidden;
    background: var(--backdrop);
  }
  .card {
    position: absolute; left: 262px; width: 686px; height: 392px;
    background: var(--card); border-radius: 20px; overflow: hidden;
  }
  .card--front { top: 165px; }
  .card--back { top: 653px; }
  .wave { position: absolute; inset: 0; width: 100%; height: 100%; }

  .brand {
    position: absolute; left: 0; right: 0; top: 100px; text-align: center;
    font-family: 'Nunito Sans', sans-serif; font-weight: 600;
    font-size: 42px; color: var(--peach-text); letter-spacing: 1px;
  }
  .person, .contact { position: absolute; color: var(--ink-white); font-family: 'Nunito Sans', sans-serif; }
  .person { left: 37px; top: 272px; }
  .person__name { font-family: 'Philosopher', sans-serif; font-weight: 700; font-size: 23px; line-height: 28px; }
  .person__role { font-size: 15px; line-height: 20px; margin-bottom: 8px; }
  .person__address { font-size: 16.5px; line-height: 21px; }
  .contact { right: 39px; top: 287px; text-align: right; font-size: 16.5px; line-height: 21.5px; }

  .appointment { position: absolute; inset: 0; font-family: 'Montserrat', sans-serif; color: var(--peach-text); }
  .appointment__title { position: absolute; left: 45px; top: 34px; font-size: 25px; font-weight: 500; }
  .book-online {
    position: absolute; left: 499px; top: 35px; width: 132px; height: 27px;
    background: var(--peach); color: #fff; border-radius: 7px;
    font-style: italic; font-weight: 800; font-size: 15px; line-height: 27px; text-align: center;
  }
  .field { position: absolute; display: flex; align-items: flex-end; font-size: 15px; font-weight: 500; }
  .field__line { flex: 1; border-bottom: 1.5px dotted var(--dots); margin: 0 6px 4px; height: 1px; }
  .field--name { left: 47px; right: 40px; top: 85px; }
  .field--date { left: 47px; right: 40px; top: 133px; }
  .field--note { left: 47px; right: 40px; top: 179px; }
  .field--extra { left: 47px; right: 40px; top: 226px; height: 20px; }
  .field--extra .field__line { margin-left: 0; margin-right: 6px; }
  .watermark {
    position: absolute; left: 0; right: 0; top: 190px; text-align: center;
    font-family: 'Nunito Sans', sans-serif; font-weight: 600; font-size: 68px;
    color: var(--peach); opacity: 0.13;
  }
  .site {
    position: absolute; left: 0; right: 0; top: 359px; text-align: center;
    font-family: 'Montserrat', sans-serif; font-style: italic; font-weight: 700;
    font-size: 15.5px; letter-spacing: 4.3px; color: #fff;
  }
</style>
</head>
<body>
  <section class="card card--front">
    <svg class="wave" viewBox="0 0 800 457" preserveAspectRatio="none" aria-hidden="true">
      <path d="M0,200 Q400,425 800,222 L800,222 Q400,448 0,228 Z" fill="var(--sage)"/>
      <path d="M0,232 Q400,440 800,218 L800,457 L0,457 Z" fill="var(--peach)" stroke="#fff" stroke-width="2"/>
    </svg>
    <div class="brand">Tidewell</div>
    <div class="person">
      <div class="person__name">Maren Holt</div>
      <div class="person__role">Physiotherapist</div>
      <div class="person__address">14 Gallivant Ave<br>Marlowe Bay 3942</div>
    </div>
    <div class="contact">
      (P) 8431 6570<br>
      (F)8431 6578<br>
      info@tidewellcareservices.com.au<br>
      tidewellcareservices.com.au
    </div>
  </section>

  <section class="card card--back">
    <div class="watermark">Tidewell</div>
    <svg class="wave" viewBox="0 0 800 457" preserveAspectRatio="none" aria-hidden="true">
      <path d="M0,278 Q400,497 800,296 L800,296 Q400,520 0,306 Z" fill="var(--sage)"/>
      <path d="M0,310 Q400,512 800,292 L800,457 L0,457 Z" fill="var(--peach)" stroke="#fff" stroke-width="2"/>
    </svg>
    <div class="appointment">
      <h2 class="appointment__title">Next Appointment</h2>
      <div class="book-online">Book Online</div>
      <div class="field field--name"><span>Name :</span><span class="field__line"></span></div>
      <div class="field field--date"><span>Date :</span><span class="field__line"></span><span>Time :</span><span class="field__line" style="flex:0 0 140px"></span><span>AM/PM</span></div>
      <div class="field field--note"><span>Note :</span><span class="field__line"></span></div>
      <div class="field field--extra"><span class="field__line"></span></div>
    </div>
    <div class="site">TIDEWELLCARESERVICES.COM.AU</div>
  </section>
</body>
</html>
```